one pager for investors

I will give an initial file in any format needed. Also, the photo that must be included. As well as the logo, that must be the key to the overall design in terms of font, colors, and general layout. I will attach a file in PDF format, which is a one pager presenting a project for investors that I would like to attract and convinced to invest in my project. What I would like you to do is propose me different and better design options, taking my first draft as an example. But you must absolutely keep every single word and number, absolutely all the information written in my first draft(except “ TEMPLATE DRAFT”). Also, on the top left corner is the logo of our company, which I think should be your main inspiration document is a one pager presented to potential investors that not only has to include the most important information in order for them to be able to see everything needed to see the value of the project (which I’ve already taken care of by writing the text needed, numbers presented and timeline shown; all of which which must be preserved in terms of content, but can be completely redesigned and manipulated ) sh a.k.a. Project summary for investor to go for it.
Serious rich investors
Real eatate

```html
<!DOCTYPE html>
<html lang="fr">
<head>
<meta charset="utf-8">
<title>Projet immobilier – résumé investisseur</title>
<link rel="stylesheet" href="https://fonts.googleapis.com/css2?family=Poppins:wght@400;600;700;800;900&family=Oswald:wght@400;500&family=Bebas+Neue&display=swap">
<style>
:root{
  --blue:#3f5bb0;
  --blue-dark:#2f4aa0;
  --navy:#141a33;
  --ink:#111;
  --grey:#555;
  --stage:#d6ccc6;
  --white:#fff;
  --black:#000;
}
*{margin:0;padding:0;box-sizing:border-box}
html,body{width:1200px;height:853px;overflow:hidden;background:var(--stage)}
.sheet{position:absolute;left:317px;top:26px;width:566px;height:800px;background:var(--white);overflow:hidden;font-family:"Poppins",sans-serif;color:var(--ink)}
.header{position:absolute;left:0;top:0;width:566px;height:136px}
.header svg{position:absolute;inset:0}
.title{position:absolute;left:0;width:100%;text-align:center;color:var(--white)}
.title-main{top:10px;font-weight:900;font-size:64px;letter-spacing:-0.5px;line-height:1}
.title-sub{top:80px;font-weight:700;font-size:31px;line-height:1}
.intro{position:absolute;left:18px;top:138px;width:535px}
.intro h2{font-weight:700;font-size:21px;color:var(--blue-dark);line-height:1.2}
.intro p{font-size:11.3px;color:var(--grey);line-height:14px;margin-top:4px}
.project-visual{position:absolute;left:0;top:229px;width:566px;height:290px;background:linear-gradient(180deg,#d9dde6 0%,#c8c6c2 35%,#8d6a55 60%,#7b7a5c 80%,#f3f3f3 100%)}
.brand-panel{position:absolute;left:237px;top:467px;width:340px;height:110px;background:var(--white);border-radius:56px 0 0 56px;box-shadow:0 2px 6px rgba(0,0,0,.08);display:flex;align-items:center;padding-left:30px;gap:12px}
.brand-dot{width:16px;height:16px;border-radius:50%;background:var(--blue-dark);flex:none}
.brand-name{font-weight:700;color:var(--navy);font-size:22px;line-height:1;white-space:nowrap}
.duration{position:absolute;left:16px;top:520px;font-family:"Bebas Neue",sans-serif;color:var(--blue-dark);font-size:30px;line-height:28px}
.tab{position:absolute;height:24px;background:var(--blue);color:var(--white);font-weight:600;font-size:14.5px;line-height:24px;padding-left:20px}
.tab-plan{left:0;top:580px;width:158px}
.tab-structure{left:273px;top:586px;width:215px;padding-left:16px;font-size:13.5px}
.figures{position:absolute;display:grid;font-size:11.3px;line-height:13.8px}
.figures b{font-weight:700}
.figures .gap{margin-top:3px}
.figures-plan{left:20px;top:607px;grid-template-columns:134px auto}
.figures-structure{left:289px;top:613px;grid-template-columns:179px auto}
.footer{position:absolute;left:0;top:745px;width:566px;height:55px}
.footer svg{position:absolute;inset:0}
.timeline{position:absolute;left:0;top:17px;height:38px;display:flex;align-items:center;padding-left:6px}
.milestone{color:var(--white);text-align:center;padding:0 8px;border-left:1px solid rgba(255,255,255,.85);line-height:1.1}
.milestone:first-child{border-left:none}
.milestone strong{display:block;font-family:"Oswald",sans-serif;font-weight:500;font-size:13px}
.milestone small{display:block;font-family:"Oswald",sans-serif;font-size:9.5px;margin-top:2px}
.imprint{position:absolute;right:16px;top:9px;color:var(--white);text-align:center;line-height:1.25;width:235px}
.imprint .label{font-size:11.5px}
.imprint .company{font-weight:700;font-size:13.5px}
.imprint .address{font-size:10.5px}
</style>
</head>
<body>
<main class="sheet">
  <header class="header">
    <svg width="566" height="136" viewBox="0 0 566 136" aria-hidden="true">
      <path d="M0 0H566V108Q566 130 520 130H60Q0 130 0 95Z" fill="var(--blue)"/>
    </svg>
    <h1 class="title title-main">CONFIDENTIEL</h1>
    <p class="title title-sub">– Projet imobilier “XXX”</p>
  </header>

  <section class="intro">
    <h2>Description du projet</h2>
    <p>Le projet XXX est un projet de dévloppement de 30 appartements de standing en PPE au centre de Lausanne. Le terrain a été sécurisé par la signature du vente à terme conditionnelle. L’objectif est d’obtenir le permis de construire, puis de ventre les lots. Dans un premier temps sur plan puis au fil de la construction.</p>
  </section>

  <div class="project-visual" role="img" aria-label="Rendu architectural de l’immeuble résidentiel de standing à balcons vitrés, entouré de végétation"></div>

  <div class="brand-panel">
    <span class="brand-dot"></span>
    <span class="brand-name">Veranor Properties SA</span>
  </div>

  <p class="duration">Durée estimée du projet<br>– 24 à 36 mois.</p>

  <div class="tab tab-plan">Plan financier</div>
  <div class="figures figures-plan">
    <span>Prix du terrain</span><span>CHF 2’000’000</span>
    <span>Frais d’acquisition</span><span>CHF 100’000</span>
    <span>Coût de construction</span><span>CHF 2’500’000</span>
    <span>Divers &amp; imprévus</span><span>CHF 200’000</span>
    <b class="gap">Prix de revient total</b><b class="gap">CHF 4’800’000</b>
    <b class="gap">Prix de vente total</b><b class="gap">CHF 7’500’000</b>
    <span>Honoraires sur vente</span><span>CHF 190’000</span>
    <b class="gap">Marge projet</b><b class="gap">CHF 2’510’000</b>
    <span>En % sur prix de vente</span><span>33.47%</span>
  </div>

  <div class="tab tab-structure">Structure d’investissement</div>
  <div class="figures figures-structure">
    <span>Besoin de fonds propres</span><span>CHF 2’000’000</span>
    <span>Retour de fonds total</span><span>CHF 3’156’600</span>
    <b>Bénéfice net investisseur</b><b>CHF 1’656’600</b>
    <span>Soit 2/3 du bénéfice projet</span><span></span>
    <b class="gap">Multiple sur fonds propres</b><b class="gap">x1.83</b>
    <b class="gap">Rendement annualisé</b><b class="gap">41.4%</b>
    <span>Calcul sur 24 mois</span><span></span>
  </div>

  <footer class="footer">
    <svg width="566" height="55" viewBox="0 0 566 55" aria-hidden="true">
      <rect x="0" y="17" width="300" height="38" fill="var(--blue)"/>
      <polygon points="290,55 300,17 306,17 296,55" fill="var(--black)"/>
      <polygon points="300,55 310,17 316,17 306,55" fill="var(--blue)"/>
      <polygon points="310,55 325,0 566,0 566,55" fill="var(--black)"/>
    </svg>
    <div class="timeline">
      <div class="milestone"><strong>08.2024</strong><small>Achat parcelle</small></div>
      <div class="milestone"><strong>04.2025</strong><small>Mise à l’enquête</small></div>
      <div class="milestone"><strong>12.2025</strong><small>Début construction</small></div>
      <div class="milestone"><strong>12.2025</strong><small>Livraison</small></div>
    </div>
    <div class="imprint">
      <div class="label">CONFIDENTIEL</div>
      <div class="company">Veranor Properties Vaud SA</div>
      <div class="address">- Chemin des Alpes 12 - CH-1110 Morges</div>
    </div>
  </footer>
</main>
</body>
</html>
```